Redesign Comparisson chart - make modern and effective

Use your imaginations to make a powerful distinction between KMV & other holistic modalities. There are 7 elements physical, mental, emotional, energetic, subconscious, superconscious and before and after testing.
We want it to be obvious that KMV is the only modality that works on all these elements simultaneously. We do not want to include any chakras as we want this information to be accepted by a wide range of people and belief systems.'

We want it to look simple but effective. Professional but powerful. We want KMV to stand out even of you eye just passed over i.
Updates

Hi everyone, thanks for your submissions so far. Basically what this image is meant to represent is a comparison chart between all the modalities There are 5 elements physical, mental, emotional, subconscious and superconscious. we want to reflect that KMV is the only modality that works on all these elements simultaneously. As we want the concept to be accepted and not considered woo woo, we want to steer away from chakras.

Target Market(s)

Professionals

Industry/Entity Type

Professional services

Font styles to use
Sans Serif
Other font styles liked:
• Poppins Monserratt

Colors
0094D4
00A9DD
6FCCEA
C7EBF8
E9F6FB

Requirements
Must have
• Clear/professional and clean look. Brand colours and logos. All typography and formats must be cohesive.
Nice to have
• More easy to read, different layout
Should not have
• Do not change the data just the way its presented. No chakras

```html
<!DOCTYPE html>
<html lang="en">
<head>
<meta charset="utf-8">
<title>KMV Modality Comparison Chart</title>
<link rel="stylesheet" href="https://fonts.googleapis.com/css2?family=Montserrat:wght@400;500;600;700&family=Oswald:wght@400;500&display=swap">
<style>
  :root{
    --brand:#29b6e6;
    --ink:#1c1c1c;
    --muted:#555;
    --grid:#b5b5b5;
    --label-bg:#e8e8e8;
    --physical:#e61f3a;
    --mental:#2dbbe9;
    --emotional:#35b34a;
    --energetic:#f07a30;
    --subconscious:#e8b43a;
    --superconscious:#7b559f;
    --testing:#cf4d9f;
  }
  *{box-sizing:border-box;margin:0;padding:0}
  html,body{width:1200px;height:1200px;overflow:hidden;background:#fff}
  body{position:relative;font-family:'Montserrat',sans-serif;color:var(--ink)}

  .brand{position:absolute;left:99px;top:50px;width:220px;text-align:center;font-weight:500;font-size:30px;color:var(--ink);line-height:1;letter-spacing:1px}
  .site{position:absolute;left:99px;top:121px;width:220px;border-top:2px solid var(--brand);border-bottom:2px solid var(--brand);height:35px;
        font-size:14px;font-weight:500;color:var(--brand);letter-spacing:0.6px;text-align:center;line-height:31px}

  .headline{position:absolute;left:340px;width:770px;top:38px;text-align:center;font-weight:700;font-size:24.5px;color:var(--brand)}
  .beliefs{position:absolute;left:340px;width:770px;top:78px;text-align:center;font-size:15.5px;font-weight:500;line-height:24.5px}

  .col-head{position:absolute;top:173px;width:110px;height:47px;border:1.5px solid;border-radius:24px;background:#fff;
            font-family:'Oswald',sans-serif;font-size:17px;line-height:17px;display:flex;align-items:center;justify-content:center;text-align:center}

  .c1{left:340px}.c2{left:450px}.c3{left:560px}.c4{left:669px}.c5{left:779px}.c6{left:889px}.c7{left:999px}
  .physical{color:var(--physical);border-color:var(--physical)}
  .mental{color:var(--mental);border-color:var(--mental)}
  .emotional{color:var(--emotional);border-color:var(--emotional)}
  .energetic{color:var(--energetic);border-color:var(--energetic)}
  .subconscious{color:var(--subconscious);border-color:var(--subconscious)}
  .superconscious{color:var(--superconscious);border-color:var(--superconscious)}
  .testing{color:var(--testing);border-color:var(--testing)}

  .row{position:absolute;left:0;width:1200px;height:0}
  .row .label{position:absolute;left:99px;width:219px;transform:translateY(-50%);background:var(--label-bg);border-radius:10px;
              text-align:center;font-size:16px;font-weight:500;line-height:18.5px;padding:3px 4px}
  .row .line{position:absolute;left:318px;width:791px;top:0;border-top:1px solid var(--grid)}
  .row .tick{position:absolute;top:-11px;height:22px;border-left:1px solid var(--grid)}
  .t1{left:340px}.t2{left:450px}.t3{left:560px}.t4{left:669px}.t5{left:779px}.t6{left:889px}.t7{left:999px}.t8{left:1108px}
  .bar{position:absolute;top:-8px;height:16px;width:110px;border-radius:8px}
  .bar.physical{background:var(--physical)}.bar.mental{background:var(--mental)}.bar.emotional{background:var(--emotional)}
  .bar.energetic{background:var(--energetic)}.bar.subconscious{background:var(--subconscious)}
  .bar.superconscious{background:var(--superconscious)}.bar.testing{background:var(--testing)}

  .row.featured .label{background:var(--brand);color:#fff;font-weight:700;font-size:16px;height:34px;line-height:28px;text-align:left;padding-left:4px}
  .row.featured .label small{font-weight:500;font-size:12px;margin-right:8px}
  .row.featured .line{border-top:2px solid #555;top:-1px}
  .row.featured .tick{border-left:2px solid #555}
  .row.featured .bar{top:-12.5px;height:25px;border-radius:12.5px}

  .notes{position:absolute;top:935px;width:285px}
  .notes h2{font-family:'Oswald',sans-serif;font-weight:400;font-size:22px;line-height:26px}
  .notes p{font-size:11px;line-height:15.3px;color:var(--muted);margin-top:3px}
  .notes h2.physical{color:var(--physical)}.notes h2.mental{color:var(--mental)}.notes h2.emotional{color:var(--emotional)}
  .notes h2.energetic{color:var(--energetic)}.notes h2.subconscious{color:var(--subconscious)}
  .notes h2.superconscious{color:var(--superconscious)}.notes h2.testing{color:var(--testing)}
</style>
</head>
<body>

<div class="brand">Lumenaria</div>
<div class="site">WWW.LUMENARIA.COM.AU</div>

<h1 class="headline">Choose KMV for fast, immediate and powerful results</h1>
<p class="beliefs">I must experience healing on all levels, I am not just a body.<br>I want to learn how to heal myself, so I’m not dependent on others.<br>I want to release all my emotional and mental blocks, so I can be the best version of myself.</p>

<div class="col-head c1 physical">PHYSICAL</div>
<div class="col-head c2 mental">MENTAL</div>
<div class="col-head c3 emotional">EMOTIONAL</div>
<div class="col-head c4 energetic">ENERGETIC</div>
<div class="col-head c5 subconscious">SUBCONSCIOUS</div>
<div class="col-head c6 superconscious">SUPER<br>CONSCIOUS</div>
<div class="col-head c7 testing">BEFORE AND<br>AFTER TESTING</div>

<div class="row" style="top:266px"><div class="line"></div><span class="tick t1"></span><span class="tick t2"></span><span class="tick t3"></span><span class="tick t4"></span><span class="tick t5"></span><span class="tick t6"></span><span class="tick t7"></span><span class="tick t8"></span>
  <div class="label" style="height:94px">Massage<br>Yoga<br>Natropathy<br>Ayurvedic Medicine<br>Western Medicine</div>
  <span class="bar physical c1"></span></div>

<div class="row" style="top:332px"><div class="line"></div><span class="tick t1"></span><span class="tick t2"></span><span class="tick t3"></span><span class="tick t4"></span><span class="tick t5"></span><span class="tick t6"></span><span class="tick t7"></span><span class="tick t8"></span>
  <div class="label">Physhic Intuitive</div>
  <span class="bar physical c1"></span><span class="bar mental c2"></span></div>

<div class="row" style="top:363px"><div class="line"></div><span class="tick t1"></span><span class="tick t2"></span><span class="tick t3"></span><span class="tick t4"></span><span class="tick t5"></span><span class="tick t6"></span><span class="tick t7"></span><span class="tick t8"></span>
  <div class="label">Psychic Constellation</div>
  <span class="bar physical c1"></span><span class="bar mental c2"></span><span class="bar energetic c4"></span></div>

<div class="row" style="top:394px"><div class="line"></div><span class="tick t1"></span><span class="tick t2"></span><span class="tick t3"></span><span class="tick t4"></span><span class="tick t5"></span><span class="tick t6"></span><span class="tick t7"></span><span class="tick t8"></span>
  <div class="label">Acupuncture</div>
  <span class="bar physical c1"></span><span class="bar energetic c4"></span></div>

<div class="row" style="top:424px"><div class="line"></div><span class="tick t1"></span><span class="tick t2"></span><span class="tick t3"></span><span class="tick t4"></span><span class="tick t5"></span><span class="tick t6"></span><span class="tick t7"></span><span class="tick t8"></span>
  <div class="label">Nutritional Healing</div>
  <span class="bar physical c1"></span><span class="bar testing c7"></span></div>

<div class="row" style="top:455px"><div class="line"></div><span class="tick t1"></span><span class="tick t2"></span><span class="tick t3"></span><span class="tick t4"></span><span class="tick t5"></span><span class="tick t6"></span><span class="tick t7"></span><span class="tick t8"></span>
  <div class="label">Chinese Medicine</div>
  <span class="bar physical c1"></span><span class="bar energetic c4"></span><span class="bar testing c7"></span></div>

<div class="row" style="top:496px"><div class="line"></div><span class="tick t1"></span><span class="tick t2"></span><span class="tick t3"></span><span class="tick t4"></span><span class="tick t5"></span><span class="tick t6"></span><span class="tick t7"></span><span class="tick t8"></span>
  <div class="label" style="line-height:21px">Kinesiology<br>Soft Tissue Therapy</div>
  <span class="bar physical c1"></span><span class="bar subconscious c5"></span><span class="bar testing c7"></span></div>

<div class="row featured" style="top:541px"><div class="line"></div><span class="tick t1"></span><span class="tick t2"></span><span class="tick t3"></span><span class="tick t4"></span><span class="tick t5"></span><span class="tick t6"></span><span class="tick t7"></span><span class="tick t8"></span>
  <div class="label"><small>KMV</small>Kinetic Mind Vitality</div>
  <span class="bar physical c1"></span><span class="bar mental c2"></span><span class="bar emotional c3"></span><span class="bar energetic c4"></span><span class="bar subconscious c5"></span><span class="bar superconscious c6"></span><span class="bar testing c7"></span></div>

<div class="row" style="top:578px"><div class="line"></div><span class="tick t1"></span><span class="tick t2"></span><span class="tick t3"></span><span class="tick t4"></span><span class="tick t5"></span><span class="tick t6"></span><span class="tick t7"></span><span class="tick t8"></span>
  <div class="label">EFT</div>
  <span class="bar physical c1"></span><span class="bar mental c2"></span><span class="bar subconscious c5"></span><span class="bar testing c7"></span></div>

<div class="row" style="top:609px"><div class="line"></div><span class="tick t1"></span><span class="tick t2"></span><span class="tick t3"></span><span class="tick t4"></span><span class="tick t5"></span><span class="tick t6"></span><span class="tick t7"></span><span class="tick t8"></span>
  <div class="label">Chiropractic</div>
  <span class="bar physical c1"></span><span class="bar energetic c4"></span><span class="bar subconscious c5"></span><span class="bar testing c7"></span></div>

<div class="row" style="top:649px"><div class="line"></div><span class="tick t1"></span><span class="tick t2"></span><span class="tick t3"></span><span class="tick t4"></span><span class="tick t5"></span><span class="tick t6"></span><span class="tick t7"></span><span class="tick t8"></span>
  <div class="label">Reiki<br>Crystal Healing</div>
  <span class="bar energetic c4"></span></div>

<div class="row" style="top:688px"><div class="line"></div><span class="tick t1"></span><span class="tick t2"></span><span class="tick t3"></span><span class="tick t4"></span><span class="tick t5"></span><span class="tick t6"></span><span class="tick t7"></span><span class="tick t8"></span>
  <div class="label">Energy Medicine</div>
  <span class="bar energetic c4"></span><span class="bar testing c7"></span></div>

<div class="row" style="top:719px"><div class="line"></div><span class="tick t1"></span><span class="tick t2"></span><span class="tick t3"></span><span class="tick t4"></span><span class="tick t5"></span><span class="tick t6"></span><span class="tick t7"></span><span class="tick t8"></span>
  <div class="label">Brainwave Healing</div>
  <span class="bar subconscious c5"></span><span class="bar superconscious c6"></span></div>

<div class="row" style="top:750px"><div class="line"></div><span class="tick t1"></span><span class="tick t2"></span><span class="tick t3"></span><span class="tick t4"></span><span class="tick t5"></span><span class="tick t6"></span><span class="tick t7"></span><span class="tick t8"></span>
  <div class="label">Psychology</div>
  <span class="bar mental c2"></span></div>

<div class="row" style="top:789px"><div class="line"></div><span class="tick t1"></span><span class="tick t2"></span><span class="tick t3"></span><span class="tick t4"></span><span class="tick t5"></span><span class="tick t6"></span><span class="tick t7"></span><span class="tick t8"></span>
  <div class="label">Mindfulness Meditation<br>Life Coaching</div>
  <span class="bar mental c2"></span><span class="bar testing c7"></span></div>

<div class="row" style="top:839px"><div class="line"></div><span class="tick t1"></span><span class="tick t2"></span><span class="tick t3"></span><span class="tick t4"></span><span class="tick t5"></span><span class="tick t6"></span><span class="tick t7"></span><span class="tick t8"></span>
  <div class="label">Hypnotherapy<br>Inner Child Healing</div>
  <span class="bar mental c2"></span><span class="bar subconscious c5"></span></div>

<div class="row" style="top:889px"><div class="line"></div><span class="tick t1"></span><span class="tick t2"></span><span class="tick t3"></span><span class="tick t4"></span><span class="tick t5"></span><span class="tick t6"></span><span class="tick t7"></span><span class="tick t8"></span>
  <div class="label">Language Patterning<br>Past Event Therapy</div>
  <span class="bar mental c2"></span><span class="bar subconscious c5"></span><span class="bar testing c7"></span></div>

<section class="notes" style="left:99px">
  <h2 class="physical">PHYSICAL</h2>
  <p>Most modalities, including, a western medicine, focus on and treat the physical body only. The KMV process enables you to engage in healing your own body during the sessions. There is no muscle testing, no hands-on healing and no herbal remedies or medicines.</p>
</section>
<section class="notes" style="left:99px;top:1071px">
  <h2 class="mental">MENTAL</h2>
  <p>KMV enables you to use your own consciousness to self-heal. We don’t give you advice or coaching, we allow your mind to heal itself.</p>
</section>
<section class="notes" style="left:448px;width:275px">
  <h2 class="emotional">EMOTIONAL</h2>
  <p>KMV is the only modality that engages your emotions on physical level. Emotions get stuck in your body and cause illness over time if left unchecked. KMV enables you to experience fast and powerful emotional releasing.</p>
</section>
<section class="notes" style="left:448px;top:1071px;width:270px">
  <h2 class="energetic">ENERGETIC</h2>
  <p>Most modalities try to move the energy in your body for you. KMV enales and empowers you to do it yourself.</p>
</section>
<section class="notes" style="left:775px;width:325px">
  <h2 class="subconscious">SUBCONSCIOUS</h2>
  <p>Some modalities, like Kinesiology, access your subconscious through muscle testing. KMV empowers you to access your own subconscious and heal it yourself.</p>
</section>
<section class="notes" style="left:775px;top:1026px;width:325px">
  <h2 class="superconscious">SUPERCONSCIOUS</h2>
  <p>KMV is the only modality that enables you to access and heal your superconscious mind yourself.</p>
</section>
<section class="notes" style="left:775px;top:1103px;width:325px">
  <h2 class="testing">BEFORE &amp; AFTER TESTING</h2>
  <p>KMV is the only modality that enables you to provide before and after results, which are documented by us, and analysed by you with our help.</p>
</section>

</body>
</html>
```